Residential Remodeling Contractor needs updated business card

I need a new design for my business card.
Name of the company is Ridgefell Construction. I need a card that commands presence, strength, integrity. I have been in business for 28 years. I am a Residential Remodeling Contractor that covers all aspects of a residential remodel and build.

```html
<!DOCTYPE html>
<html lang="en">
<head>
<meta charset="utf-8">
<title>Ridgefell Construction — Business Card</title>
<link rel="stylesheet" href="https://fonts.googleapis.com/css2?family=Noto+Serif:ital,wght@0,700;1,700&family=Arimo:ital,wght@0,400;1,400&display=swap">
<style>
  :root {
    --navy: #1b3e7c;
    --navy-deep: #173a78;
    --ink: #2a2a2a;
    --muted: #555a63;
    --paper: #ffffff;
    --backdrop: #2b2b2d;
  }
  * { box-sizing: border-box; margin: 0; padding: 0; }
  html, body { width: 1200px; height: 878px; overflow: hidden; }
  body {
    background: var(--backdrop);
    font-family: "Arimo", Arial, sans-serif;
    position: relative;
  }
  .card {
    position: absolute;
    top: 285px;
    width: 540px;
    height: 308px;
    box-shadow: 0 10px 30px rgba(0,0,0,.45);
  }
  .card--front { left: 40px; background: var(--paper); }
  .card--back { left: 620px; background: var(--navy-deep); }

  .wordmark {
    position: absolute;
    display: flex;
    align-items: center;
    gap: 12px;
    font-family: "Noto Serif", Georgia, serif;
    font-weight: 700;
    text-transform: uppercase;
    line-height: 1.05;
  }
  .wordmark__dot { flex: none; border-radius: 50%; }
  .wordmark__text span { display: block; }

  .card--front .wordmark { right: 34px; top: 50px; color: var(--navy); }
  .card--front .wordmark__dot { width: 16px; height: 16px; background: var(--navy); }
  .card--front .wordmark__text { font-size: 22px; letter-spacing: 1px; }
  .card--front .wordmark__text span + span { font-size: 17px; letter-spacing: 1.5px; }

  .card--back .wordmark { left: 50%; top: 50%; transform: translate(-50%, -50%); color: var(--paper); }
  .card--back .wordmark__dot { width: 22px; height: 22px; background: var(--paper); }
  .card--back .wordmark__text { font-size: 34px; letter-spacing: 1.5px; }
  .card--back .wordmark__text span + span { font-size: 26px; letter-spacing: 2px; }

  .holder { position: absolute; left: 52px; top: 136px; }
  .holder__name {
    font-family: "Noto Serif", Georgia, serif;
    font-style: italic;
    font-weight: 700;
    font-size: 25px;
    color: var(--navy);
    letter-spacing: .5px;
  }
  .holder__role { font-style: italic; font-size: 13px; color: var(--muted); margin-top: 1px; }

  .rule { position: absolute; left: 52px; right: 40px; top: 202px; height: 1.5px; background: var(--navy); }

  .contacts { position: absolute; left: 52px; top: 220px; list-style: none; }
  .contacts li {
    display: flex; align-items: center; gap: 8px;
    font-size: 13px; color: var(--ink); height: 21px; font-style: italic;
  }
  .contacts svg { width: 11px; height: 11px; fill: var(--navy); flex: none; }

  .divider { position: absolute; left: 296px; top: 238px; width: 1.5px; height: 42px; background: var(--navy); }

  .address { position: absolute; left: 312px; top: 240px; font-size: 13px; line-height: 21px; color: var(--ink); }
</style>
</head>
<body>
  <section class="card card--front" aria-label="Business card front">
    <div class="wordmark">
      <span class="wordmark__dot"></span>
      <div class="wordmark__text"><span>Ridgefell</span><span>Construction</span></div>
    </div>

    <div class="holder">
      <h1 class="holder__name">DANIEL OKAFOR</h1>
      <p class="holder__role">Owner &amp; Manager</p>
    </div>

    <div class="rule"></div>

    <ul class="contacts">
      <li>
        <svg viewBox="0 0 12 12" aria-hidden="true"><path d="M1 4c0-2 2-3 5-3s5 1 5 3l-2 1-1-1.5H4L3 5zM3 6h6l1 5H2z"/></svg>
        555 014 2387
      </li>
      <li>
        <svg viewBox="0 0 12 12" aria-hidden="true"><path d="M0 2h12v8H0zM1 3v.3L6 7l5-3.7V3z" fill-rule="evenodd"/></svg>
        info@ridgefellconstruction.com
      </li>
      <li>
        <svg viewBox="0 0 12 12" aria-hidden="true"><circle cx="6" cy="6" r="5.5"/><path d="M2 4h8M2 8h8M6 .5v11" stroke="#fff" stroke-width=".8" fill="none"/></svg>
        www.ridgefellconstruction.com
      </li>
    </ul>

    <div class="divider"></div>

    <address class="address" style="font-style:normal">
      P.O. Box&nbsp; Street Name<br>
      Country Name AB, A5B 521
    </address>
  </section>

  <section class="card card--back" aria-label="Business card back">
    <div class="wordmark">
      <span class="wordmark__dot"></span>
      <div class="wordmark__text"><span>Ridgefell</span><span>Construction</span></div>
    </div>
  </section>
</body>
</html>
```